Alterations to existing business card

Here is my current logo and I want the "cafe and bar" taken off with just the words Lumo and our slogan "SAVOUR THE MOMENT" on the card, Plus the logo.
Our Current Business Card is currently 5.5cm by 5.5cm and would like it to remain like this thanks.
The loyalty card can be 10 squares with the logo specifying the 10th coffee free. I would like the cheapest option please.
Also on our business card would like the Facebook logo and instagram Logo with TAZALUMO27 as link to our photos on instagram.

Keep Colour schemes the same please.

On the business cards

Dale Brinton Director
0427916038
dale27lumo@mailvista.test

Paula Ferrisi Principal
0428571963
paulumo@mailvista.test

Thanks Dale

Industry/Entity Type

Business

```html
<!DOCTYPE html>
<html lang="en">
<head>
<meta charset="utf-8">
<title>Lumo business card</title>
<link rel="stylesheet" href="https://fonts.googleapis.com/css2?family=Open+Sans:wght@400;600&display=swap">
<style>
  :root {
    --page: #ececea;
    --card: #ffffff;
    --ink: #111111;
    --gold: #e9a83b;
    --gold-soft: #e3ae4e;
    --stripe: #f5cf63;
    --band: #eea73c;
    --social: #8a8f99;
  }
  * { margin: 0; padding: 0; box-sizing: border-box; }
  html, body { width: 1189px; height: 1200px; overflow: hidden; background: var(--page); }
  body { position: relative; font-family: "Open Sans", Arial, sans-serif; color: var(--ink); }

  .card {
    position: absolute; left: 140px; width: 915px; height: 522px;
    background: var(--card); border-radius: 38px; overflow: hidden;
  }
  .card--front { top: 45px; }
  .card--back { top: 624px; }

  .swoosh { position: absolute; left: 0; top: 0; width: 915px; height: 522px; }

  .person { position: absolute; left: 38px; }
  .person--director { top: 44px; }
  .person--principal { top: 262px; }
  .person__name { font-size: 42px; font-weight: 600; color: var(--gold); line-height: 50px; }
  .person__role { font-size: 29px; line-height: 36px; margin-bottom: 22px; }
  .contact { display: flex; align-items: center; font-size: 28px; line-height: 36px; }
  .contact__icon { width: 22px; height: 22px; margin-right: 18px; flex: none; }

  .brand { position: absolute; }
  .brand__mark { position: absolute; border: 3px solid var(--gold); border-radius: 50%; }
  .brand__name { position: absolute; font-weight: 400; color: var(--ink); letter-spacing: 2px; line-height: 1; }
  .brand__tagline { position: absolute; color: var(--gold-soft); white-space: nowrap; line-height: 1; }

  .card--front .brand__mark { left: 458px; top: 35px; width: 134px; height: 134px; }
  .card--front .brand__name { left: 602px; top: 56px; font-size: 80px; }
  .card--front .brand__tagline { left: 606px; top: 140px; font-size: 21px; letter-spacing: 3px; }

  .card--back .brand__mark { left: 144px; top: 112px; width: 266px; height: 266px; border-width: 4px; }
  .card--back .brand__name { left: 432px; top: 182px; font-size: 92px; }
  .card--back .brand__tagline { left: 437px; top: 283px; font-size: 26px; letter-spacing: 4px; }

  .social { position: absolute; left: 609px; display: flex; align-items: center; }
  .social--one { top: 228px; }
  .social--two { top: 285px; }
  .social__handle { font-size: 33px; letter-spacing: 1px; width: 193px; line-height: 42px; }
  .social__badge { width: 41px; height: 41px; border-radius: 7px; background: var(--social); }
</style>
</head>
<body>

<section class="card card--front">
  <svg class="swoosh" viewBox="0 0 915 522" aria-hidden="true">
    <path fill="var(--stripe)" d="M0,455 C300,505 650,470 915,298 L915,322 C680,478 320,536 0,497 Z"/>
    <path fill="var(--band)" d="M0,515 C330,542 700,485 915,340 L915,522 L0,522 Z"/>
  </svg>

  <div class="person person--director">
    <p class="person__name">Dale Brinton</p>
    <p class="person__role">Director</p>
    <p class="contact">
      <svg class="contact__icon" viewBox="0 0 22 22" aria-hidden="true"><rect width="22" height="22" fill="var(--ink)"/><path d="M7,4 L10,7 L8.5,9 Q10,13 13,14.5 L15,13 L18,16 L16,18 Q9,18 5,10 Q4.5,6 7,4 Z" fill="#fff"/></svg>
      0427916038
    </p>
    <p class="contact">
      <svg class="contact__icon" viewBox="0 0 22 22" aria-hidden="true"><rect width="22" height="22" fill="var(--ink)"/><rect x="4" y="6" width="14" height="10" fill="none" stroke="#fff" stroke-width="1.6"/><path d="M4,6 L11,12 L18,6" fill="none" stroke="#fff" stroke-width="1.6"/></svg>
      dale27lumo@mailvista.test
    </p>
  </div>

  <div class="person person--principal">
    <p class="person__name">Paula Ferrisi</p>
    <p class="person__role">Principal</p>
    <p class="contact">
      <svg class="contact__icon" viewBox="0 0 22 22" aria-hidden="true"><rect width="22" height="22" fill="var(--ink)"/><path d="M7,4 L10,7 L8.5,9 Q10,13 13,14.5 L15,13 L18,16 L16,18 Q9,18 5,10 Q4.5,6 7,4 Z" fill="#fff"/></svg>
      0428571963
    </p>
    <p class="contact">
      <svg class="contact__icon" viewBox="0 0 22 22" aria-hidden="true"><rect width="22" height="22" fill="var(--ink)"/><rect x="4" y="6" width="14" height="10" fill="none" stroke="#fff" stroke-width="1.6"/><path d="M4,6 L11,12 L18,6" fill="none" stroke="#fff" stroke-width="1.6"/></svg>
      paulumo@mailvista.test
    </p>
  </div>

  <div class="brand">
    <span class="brand__mark"></span>
    <span class="brand__name">LUMO</span>
    <span class="brand__tagline">SAVOUR THE MOMENT</span>
  </div>

  <div class="social social--one">
    <span class="social__handle">27 LUMO</span>
    <span class="social__badge"></span>
  </div>
  <div class="social social--two">
    <span class="social__handle">27 LUMO</span>
    <span class="social__badge"></span>
  </div>
</section>

<section class="card card--back">
  <div class="brand">
    <span class="brand__mark"></span>
    <span class="brand__name">LUMO</span>
    <span class="brand__tagline">SAVOUR THE MOMENT</span>
  </div>
</section>

</body>
</html>
```